Dental Practice Billboard Design

We are a newer dental practice in need of a simple but appealing billboard for our growing dental practice to attract new patients. The practice is owned by husband and wife dentists and is family friendly in a small town in Kentucky. We try to be very friendly and caring to our patients. Would prefer a blue background for the billboard and our tooth logo to be prominent. We are partial to the Patua One font used in the image below but please feel free to tweak it as you deem necessary. The shape of the uppercase D and lowercase g are why we like that font, so fonts with a similarly shaped “D” and “g” would work as well. Please include our phone number (555) 847-1390. Please see our website Harlowbrookdentistry.example for more info on the practice if needed. Thank you! Looking forward to seeing your creation.
Updates

The dimensions will be 12ft x 24ft (3.6576m x 7.3152m). Apologies for not including this in the original prompt. Thank you all for your submissions.

Industry/Entity Type

Dental

Font styles to use
Other font styles liked:
• Patua One

Colors
0054AA
0677BA
7BADD7
CADEEF
E8F1F8
0094D4
00A9DD
6FCCEA
C7EBF8
E9F6FB
00AB8E
00BBA5
67D7C9
C6EFE9
E9F9F6
59FF00
82FF00
B8FF75
E3FFCB
F4FFEA

Requirements
Must have
• Phone number, website, Logo, Practice name “Harlow Brook Dentistry”
Should not have
• A tagline or slogan

```html
<!DOCTYPE html>
<html lang="en">
<head>
<meta charset="UTF-8">
<title>Harlow Brook Dentistry – Billboard</title>
<link rel="stylesheet" href="https://fonts.googleapis.com/css2?family=Patua+One&family=Poppins:wght@500;600;700&display=swap">
<style>
  :root {
    --canvas-bg: #9a9a9a;
    --brand-blue: #0054aa;
    --pill-green: #22b02a;
    --bullet-green: #82ff00;
    --white: #ffffff;
    --ink-blue: #0054aa;
    --photo-light: #eef1f4;
    --photo-mid: #c9ced4;
  }
  * { box-sizing: border-box; margin: 0; padding: 0; }
  html, body { width: 894px; height: 1200px; overflow: hidden; }
  body {
    background: var(--canvas-bg);
    position: relative;
    font-family: 'Poppins', sans-serif;
  }
  .billboard {
    position: absolute;
    left: 0; top: 360px;
    width: 894px; height: 480px;
    background: var(--white);
    overflow: hidden;
  }
  .billboard__blue {
    position: absolute;
    left: 238px; top: 0;
    width: 656px; height: 480px;
    background: var(--brand-blue);
  }
  .brand {
    position: absolute;
    left: 34px; top: 38px;
    display: flex; align-items: center; gap: 10px;
  }
  .brand__dot {
    width: 30px; height: 30px; border-radius: 50%;
    background: var(--brand-blue);
    flex: none;
  }
  .brand__name {
    font-family: 'Patua One', serif;
    font-size: 22px; line-height: 1.05;
    color: var(--ink-blue);
    width: 150px;
  }
  .family-photo {
    position: absolute;
    left: 40px; top: 118px;
    width: 352px; height: 362px;
    background: linear-gradient(180deg, var(--photo-light), var(--photo-mid));
  }
  .offer {
    position: absolute;
    left: 404px; top: 0;
    width: 480px; height: 480px;
    display: flex; flex-direction: column; align-items: center; justify-content: center;
    gap: 22px;
  }
  .services-pill {
    width: 200px; height: 38px;
    border-radius: 19px;
    background: var(--pill-green);
    color: var(--white);
    font-family: 'Patua One', serif;
    font-size: 24px; line-height: 38px;
    text-align: center;
  }
  .services {
    display: grid;
    grid-template-columns: 140px 165px 150px;
    row-gap: 12px;
    list-style: none;
  }
  .services li {
    display: flex; align-items: center; gap: 10px;
    color: var(--white);
    font-size: 17px; font-weight: 500; line-height: 22px;
    white-space: nowrap;
  }
  .services li::before {
    content: ""; width: 9px; height: 9px; border-radius: 50%;
    background: var(--bullet-green); flex: none;
  }
  .contact-phone {
    display: flex; align-items: center; gap: 10px;
    color: var(--white);
    font-size: 44px; font-weight: 600; line-height: 54px;
    margin-top: 6px;
  }
  .contact-phone svg { width: 36px; height: 36px; flex: none; }
  .contact-web {
    margin-top: -14px;
    color: var(--white);
    font-size: 24px; font-weight: 600;
    white-space: nowrap;
  }
</style>
</head>
<body>
  <section class="billboard">
    <div class="billboard__blue"></div>

    <div class="brand">
      <span class="brand__dot"></span>
      <span class="brand__name">Harlow Brook Dentistry</span>
    </div>

    <div class="family-photo" role="img" aria-label="Photo of a smiling family of four: father holding a toddler, mother and young daughter"></div>

    <div class="offer">
      <div class="services-pill">Our Services</div>
      <ul class="services">
        <li>Crowns</li><li>Bridges</li><li>Fillings</li>
        <li>Root Canals</li><li>Clear Aligners</li><li>Cleanings</li>
        <li>Extractions</li><li>Veneers</li><li>Dentures</li>
        <li>Implants</li><li>Whitening</li><li>Overdentures</li>
      </ul>
      <div class="contact-phone">
        <svg viewBox="0 0 34 34" aria-hidden="true">
          <circle cx="17" cy="17" r="16" fill="#22b02a"/>
          <circle cx="17" cy="17" r="12" fill="none" stroke="#ffffff" stroke-width="2"/>
          <path d="M12.5 10.5c.8-.6 1.8-.4 2.3.4l1.3 2.2c.4.7.2 1.5-.4 2l-.9.7c.7 1.6 1.9 2.9 3.5 3.7l.8-.9c.5-.6 1.4-.7 2-.3l2.2 1.3c.8.5 1 1.5.4 2.3l-.8 1c-.8.9-2 1.2-3.1.8-4.3-1.6-7.2-4.6-8.6-8.9-.3-1.1 0-2.3.9-3z" fill="#ffffff"/>
        </svg>
        <span>(555) 847-1390</span>
      </div>
      <div class="contact-web">harlowbrookdentistry.example</div>
    </div>
  </section>
</body>
</html>
```